Company identity deisgn should support 2 languages

I would like to get our company identity design
This includes the following only
Business Cards 2 languages Arabic and English
Email signature
Letterhead
Linkedin profile images
Attached is the logo in Ai format

Requirements
Must have
• For business card
Must have
Name and Adrees in arabic
Name and Address in english
You might use both side of the card
Should not have
• Any pictures other than the logo

```html
<!DOCTYPE html>
<html lang="en">
<head>
<meta charset="utf-8">
<title>Cedarline Systems – Business Cards</title>
<link rel="stylesheet" href="https://fonts.googleapis.com/css2?family=Poppins:wght@400;500&family=Cairo:wght@500;600&display=swap">
<style>
  :root {
    --blue: #1474bf;
    --grey-band: #aeb0b4;
    --ink: #3a3a3a;
    --muted: #8c8c8c;
    --rule: #8e8e8e;
    --page: #ececec;
    --card: #ffffff;
  }
  * { margin: 0; padding: 0; box-sizing: border-box; }
  html, body { width: 1200px; height: 1200px; overflow: hidden; }
  body {
    background: var(--page);
    font-family: "Poppins", sans-serif;
    color: var(--ink);
    position: relative;
  }
  .card {
    position: absolute;
    left: 200px;
    width: 800px;
    height: 457px;
    background: var(--card);
    border-radius: 34px;
    overflow: hidden;
  }
  .card--en { top: 120px; }
  .card--ar { top: 623px; }

  .brand {
    position: absolute;
    right: 42px;
    top: 68px;
    display: flex;
    align-items: center;
    gap: 12px;
    color: var(--blue);
    font-weight: 500;
    font-size: 24px;
    letter-spacing: 0.5px;
  }
  .brand__dot {
    width: 26px; height: 26px;
    border-radius: 50%;
    background: var(--blue);
  }

  .person { position: absolute; left: 44px; }
  .person__name {
    color: var(--blue);
    font-weight: 500;
    font-size: 26px;
    line-height: 1.1;
  }
  .person__role {
    color: var(--muted);
    font-size: 18px;
    line-height: 1.4;
  }
  .card--en .person { top: 226px; }
  .card--ar .person { top: 205px; }
  .card--ar .person__name { font-family: "Cairo", sans-serif; font-weight: 600; font-size: 26px; }
  .card--ar .person__role { font-family: "Cairo", sans-serif; font-weight: 500; font-size: 18px; line-height: 1.1; }

  .rule {
    position: absolute;
    left: 46px;
    height: 2px;
    background: var(--rule);
  }
  .card--en .rule { top: 298px; width: 712px; }
  .card--ar .rule { top: 284px; width: 700px; height: 1px; background: #c9c9c9; }

  .contacts {
    position: absolute;
    left: 46px;
    list-style: none;
    font-size: 18px;
    line-height: 23px;
  }
  .card--en .contacts { top: 318px; }
  .card--ar .contacts { top: 305px; left: 48px; }
  .contacts li { display: flex; align-items: center; gap: 9px; }
  .contacts svg { width: 15px; height: 15px; fill: var(--blue); flex: none; }

  .address {
    position: absolute;
    right: 42px;
    text-align: right;
    font-size: 18px;
    line-height: 23px;
  }
  .card--en .address { top: 359px; }
  .card--ar .address { top: 316px; right: 48px; line-height: 28px; }
  .address .ar { font-family: "Cairo", sans-serif; font-weight: 500; font-size: 16px; }

  .footer { position: absolute; left: 0; bottom: 0; width: 800px; height: 40px; }
  .footer__url {
    position: absolute;
    right: 30px;
    bottom: 8px;
    color: #fff;
    font-size: 19px;
  }
</style>
</head>
<body>

  <!-- English side -->
  <section class="card card--en" aria-label="Business card, English">
    <div class="brand"><span class="brand__dot"></span><span>CEDARLINE SYSTEMS</span></div>

    <div class="person">
      <p class="person__name">DANIEL HART</p>
      <p class="person__role">President</p>
    </div>

    <div class="rule"></div>

    <ul class="contacts">
      <li><svg viewBox="0 0 16 16"><path d="M3.5 1l3 3-1.7 1.8a10 10 0 0 0 5.4 5.4L12 9.5l3 3-2 2.3C6.8 14.5 1.5 9.2 1.2 3z"/></svg>555-214-7730</li>
      <li><svg viewBox="0 0 16 16"><path d="M4 0h8a1 1 0 0 1 1 1v14a1 1 0 0 1-1 1H4a1 1 0 0 1-1-1V1a1 1 0 0 1 1-1zm1 2v10h6V2z"/></svg>555-618-2049</li>
      <li><svg viewBox="0 0 16 16"><path d="M4 1h8v4H4zM1 6h14v7h-3v2H4v-2H1zm4 5v3h6v-3z"/></svg>555-307-4462</li>
      <li><svg viewBox="0 0 16 16"><path d="M1 3h14v10H1zm1.5 1.5L8 9l5.5-4.5z"/></svg>info@cedarlinesystems.com</li>
    </ul>

    <address class="address" style="font-style:normal">
      4120 Willow Creek Road<br>Fairbanks, Alaska 99701
    </address>

    <svg class="footer" viewBox="0 0 800 40" aria-hidden="true">
      <rect x="0" y="12" width="800" height="28" fill="var(--blue)"/>
      <path d="M0 0 H500 Q492 12 480 12 H0 Z" fill="var(--grey-band)"/>
      <path d="M0 12 H480 Q492 12 500 0 H0 Z" fill="var(--grey-band)"/>
      <path d="M500 0 L800 0 L800 0 Z" fill="none"/>
    </svg>
    <svg class="footer" viewBox="0 0 800 40" aria-hidden="true" style="height:40px">
      <path d="M0 0 H496 Q486 13 470 13 H0 Z" fill="var(--grey-band)"/>
      <path d="M496 0 H800 V-2 Z" fill="none"/>
    </svg>
    <svg class="footer" viewBox="0 0 800 40" aria-hidden="true" style="bottom:0;height:40px">
      <path d="M520 0 H800 V40 H0 V26 H490 Q505 26 512 12 Q516 0 530 0 Z" fill="var(--blue)"/>
    </svg>
    <span class="footer__url">cedarlinesystems.com</span>
  </section>

  <!-- Arabic side -->
  <section class="card card--ar" aria-label="Business card, Arabic">
    <div class="brand"><span class="brand__dot"></span><span>CEDARLINE SYSTEMS</span></div>

    <div class="person" dir="rtl">
      <p class="person__name">دانيال هارت</p>
      <p class="person__role" style="text-align:right">رئيس</p>
    </div>

    <div class="rule"></div>

    <ul class="contacts">
      <li><svg viewBox="0 0 16 16"><path d="M3.5 1l3 3-1.7 1.8a10 10 0 0 0 5.4 5.4L12 9.5l3 3-2 2.3C6.8 14.5 1.5 9.2 1.2 3z"/></svg>555-214-7730</li>
      <li><svg viewBox="0 0 16 16"><path d="M4 0h8a1 1 0 0 1 1 1v14a1 1 0 0 1-1 1H4a1 1 0 0 1-1-1V1a1 1 0 0 1 1-1zm1 2v10h6V2z"/></svg>555-618-2049</li>
      <li><svg viewBox="0 0 16 16"><path d="M4 1h8v4H4zM1 6h14v7h-3v2H4v-2H1zm4 5v3h6v-3z"/></svg>555-307-4462</li>
      <li><svg viewBox="0 0 16 16"><path d="M1 3h14v10H1zm1.5 1.5L8 9l5.5-4.5z"/></svg>info@cedarlinesystems.com</li>
    </ul>

    <address class="address" style="font-style:normal">
      <span class="ar" dir="rtl">4120 طريق ويلو كريك</span><br>
      <span class="ar" dir="rtl">فيربانكس، ألاسكا 99701</span><br>
      cedarlinesystems.com
    </address>

    <svg class="footer" viewBox="0 0 800 40" aria-hidden="true">
      <rect x="0" y="12" width="800" height="28" fill="var(--blue)"/>
      <path d="M0 0 H496 Q486 13 470 13 H0 Z" fill="var(--grey-band)"/>
      <path d="M520 0 H800 V40 H0 V26 H490 Q505 26 512 12 Q516 0 530 0 Z" fill="var(--blue)"/>
    </svg>
    <span class="footer__url">cedarlinesystems.com</span>
  </section>

</body>
</html>
```